energy rating company

Web Design graphics and layout only

To create two pages for the website. First the home page and the second is the design for the job board for our clients use after login. I have attached files that explain in detail what the pages should have and the purpose/desires of each object. Please read these thoroughly.

The webpages need to be clean, professional, easy on the eye, obvious in all its buttons and functions with a strong call to action on the home page and branding and clean, great and obvious looking buttons and very simple but dynamic as well. We wish to be seen as contemporary.

Business Concept

Our business concept is simple, to build a website whereby our clients will be able to upload jobs for energy raters to quote on and subsequent complete the work if their quote is selected. To link energy ratings that are required with energy raters via our website. Similarly to the velk website, jobs will be “advertised” on the job board and raters will select which jobs they wish to quote for.

I have attached a Word document explaining all the parts of the website and another word document showing what we are sort of after and a excel spreadsheet as well. Please read these in conjunction with this brief!
Updates

Dear All

I have submitted with my brief a word doc and excel spreadsheet of the two pages I want created.  However this is not the layout or design I want, I only put it together so that you will need to know what is required on each page.  Feel free to change and redesign it all.

Also the second page does not require the "process" logo or any other menu items except the first five being Home, How it works, About Us, testimonials and Contact us as per the home page.

We also are looking for something very professional and very clean.  It should be very easy to see exactly what you are looking for.

I will also extend the deadline for new designers!!  I am excited to see your talents!!

Thanks

I have increase budget and posted a note saying feel free to change all the details layout etc on my brief just include everything!!! 

Wanting a professional corporate look...

Want a professional corporate look

We have changed our minds and you we no longer require the process to be on the home page.

Thanks

Target Market(s)

Target Market

Home Inspection Companies
Pest Inspection Companies
Residential home buyers/sellers
Real Estate companies

Industry/Entity Type

It Company

Number of Pages Required

1 page

Requirements
Must have
• Colours and Styles

• The website should be mainly white as I believe it is seen as clean and simple with colour from the logos, but can be swayed if it projects the image we are after.

• It should be obvious and process orientated and I do believe symbols, pictures, etc should replace words where possible.

```html
<!DOCTYPE html>
<html lang="en">
<head>
<meta charset="utf-8">
<title>Corvane Australia – Home and Job Board</title>
<link href="https://fonts.googleapis.com/css2?family=Didact+Gothic&family=Open+Sans:wght@400;600;700&family=Ubuntu:wght@300;500;700&display=swap" rel="stylesheet">
<style>
:root{
  --green:#2f7f1f;
  --green-dark:#1d5e12;
  --green-light:#4aa332;
  --orange:#df6a17;
  --orange-dark:#b9520f;
  --orange-light:#f39a45;
  --grey-band:#ebebeb;
  --charcoal:#3b3b3b;
  --text:#3e3e3e;
  --muted:#777;
  --line:#d9d9d9;
  --panel:#f3f3f3;
}
*{box-sizing:border-box;margin:0;padding:0}
html,body{width:1200px;height:2772px;overflow:hidden}
body{position:relative;background:var(--grey-band);font-family:"Open Sans",sans-serif;color:var(--text)}
.label-band{position:absolute;left:0;width:1200px;display:flex;align-items:center;justify-content:center;font-family:"Didact Gothic",sans-serif;font-size:54px;letter-spacing:2px;color:#5a5a5a;background:var(--grey-band)}
.site{position:absolute;left:0;width:1200px}
.green-bar{position:absolute;left:0;top:0;width:1200px;height:20px;background:linear-gradient(var(--green-light),var(--green-dark))}
.dark-band{position:absolute;left:0;top:205px;width:1200px;height:213px;background:linear-gradient(#4a4a4a,#2f2f2f)}
.page{position:absolute;left:113px;top:20px;width:974px;background:#fff;box-shadow:0 0 10px rgba(0,0,0,.25)}
.header{position:absolute;left:0;top:0;width:974px;height:179px;background:linear-gradient(#fff,#f4f4f4);border-bottom:3px solid #333}
.nav{position:absolute;left:380px;top:0;width:570px;height:27px;background:linear-gradient(var(--green-light),var(--green));border-radius:0 0 4px 4px;display:flex;justify-content:center;align-items:center;font-family:"Didact Gothic",sans-serif;font-size:14px;color:#fff;box-shadow:0 2px 3px rgba(0,0,0,.2)}
.nav span{padding:0 9px}
.nav i{font-style:normal;opacity:.8}
.brand{position:absolute;left:34px;top:44px;display:flex;align-items:center;gap:12px}
.brand-mark{width:48px;height:48px;border-radius:50%;background:var(--orange)}
.brand-name{font-family:"Ubuntu",sans-serif;font-weight:700;font-size:34px;color:var(--orange);line-height:1}
.quick{position:absolute;top:52px;width:120px;text-align:center;font-family:"Didact Gothic",sans-serif;font-size:13px;color:#333}
.quick .icon{width:66px;height:70px;margin:0 auto 10px;border-radius:6px}
.quick small{display:block;font-size:8px;line-height:1}
.icon-quote{background:linear-gradient(135deg,#9cc4ea,#3d79c2)}
.icon-raters{background:linear-gradient(135deg,#a7c77f,#4f7fb6)}
.icon-board{background:linear-gradient(#6fbf3d,#2e7a1d)}
.hero{position:absolute;left:0;top:185px;width:974px;height:213px;background:linear-gradient(var(--orange-dark),var(--orange) 60%,var(--orange-light))}
.hero-fade{position:absolute;left:0;top:398px;width:974px;height:60px;background:linear-gradient(#f9c79a,#fff)}
.step{position:absolute;top:46px;width:172px;height:107px;background:linear-gradient(#fff,#e6e6e6);border-radius:4px;box-shadow:0 2px 4px rgba(0,0,0,.35)}
.step::after{content:"";position:absolute;left:0;top:113px;width:172px;height:48px;background:linear-gradient(rgba(255,255,255,.25),rgba(255,255,255,0));border-radius:4px}
.step-num{position:absolute;left:-6px;top:-10px;width:22px;height:22px;border-radius:50%;background:#fff;border:2px solid #444;font:600 13px/18px "Open Sans",sans-serif;text-align:center;color:#222}
.step-text{position:absolute;left:12px;bottom:8px;font-family:"Didact Gothic",sans-serif;font-size:16px;color:#444;line-height:1.05}
.step-text b{display:block;font-weight:400;font-size:27px;color:var(--orange)}
.content-title{position:absolute;left:36px;font-family:"Ubuntu",sans-serif;font-weight:300;font-size:29px;color:var(--orange)}
.intro{position:absolute;left:36px;top:508px;width:340px;font-size:11.5px;line-height:1.2;color:#444}
.intro p{margin-bottom:13px}
.wide{position:absolute;left:36px;width:567px;font-size:11.5px;line-height:1.2;color:#444}
.team-photo{position:absolute;left:384px;top:508px;width:219px;height:143px;background:linear-gradient(#eef2f4,#9aa8b0 70%,#c9d8d6)}
.benefits{position:absolute;left:36px;top:721px;width:567px;list-style:none}
.benefits li{height:25.4px;display:flex;align-items:center;padding-left:12px;font-size:11.5px;font-weight:600;color:#333;background:linear-gradient(90deg,#f3f3f3,#fafafa);border-bottom:1px solid #fff}
.benefits li::before{content:"";width:11px;height:11px;background:#333;margin-right:24px}
.box{position:absolute;left:674px;width:259px;background:var(--panel);border:1px solid #ddd;border-radius:3px;padding:10px 16px}
.box h3{font-family:"Ubuntu",sans-serif;font-weight:700;font-size:24px;color:var(--orange);margin-bottom:8px}
.box label{display:block;font-size:11.5px;font-weight:700;color:#222;margin-bottom:4px}
.field{height:27px;background:#fff;border:1px solid #ccc;margin-bottom:14px}
.forgot{text-align:right;font-size:10px;color:#222;margin:-12px 0 5px}
.btn{display:block;width:98px;height:28px;margin:0 auto;background:linear-gradient(var(--green-light),var(--green-dark));border-radius:3px;color:#fff;font-size:12px;font-weight:700;text-align:center;line-height:28px}
.testimonial{font-size:10.5px;line-height:1.7;color:#777;margin-bottom:18px}
.testimonial cite{display:block;font-style:normal;font-weight:700;margin-top:16px;color:#666}
.footer{position:absolute;left:0;width:974px;height:42px;background:linear-gradient(var(--green-light),var(--green-dark));display:flex;justify-content:flex-end;align-items:center;padding-right:32px;font-size:10px;font-weight:700;color:#fff}
.footer span{padding:0 6px}
.account{position:absolute;left:36px;top:525px;display:flex;gap:6px;font-size:11.5px;color:#555}
.account-labels{width:128px;height:181px;border:1px solid var(--line);background:#f7f7f7;padding:3px 4px;line-height:23.5px}
.account-values{width:574px;height:181px;border:1px solid var(--line);background:#f0f0f0;padding:14px 12px;line-height:23.5px}
.tabs{position:absolute;left:36px;top:760px;display:flex;gap:11px}
.tab{width:217px;height:51px;border-radius:4px 4px 0 0;background:linear-gradient(#fafafa,#ececec);font-family:"Ubuntu",sans-serif;font-weight:700;font-size:17px;color:var(--orange);display:flex;align-items:center;justify-content:center}
.tab.active{background:linear-gradient(#3a3a3a,#111);color:#fff}
.jobs-panel{position:absolute;left:36px;top:811px;width:904px;height:360px;border:1px solid var(--line);border-radius:0 0 4px 4px;background:#fff;padding:10px 8px}
.jobs{border-collapse:separate;border-spacing:0;width:884px;background:var(--panel)}
.jobs th{height:48px;background:linear-gradient(#dedede,#b9b9b9);font-size:10px;font-weight:700;letter-spacing:.5px;color:#555;text-transform:uppercase;line-height:1.2}
.jobs td{padding:2.5px 5px;border-right:1px solid #fff}
.jobs tr:nth-child(2) td{padding-top:12px}
.jobs td div{height:18px;background:#e6e6e6;border:1px solid #cfcfcf;border-radius:2px;font-size:11.5px;color:#555;text-align:center;line-height:16px}
</style>
</head>
<body>

<div class="label-band" style="top:0;height:102px">HOME PAGE</div>

<section class="site" style="top:102px;height:1181px">
  <div class="green-bar"></div>
  <div class="dark-band"></div>
  <div class="page" style="height:1161px">
    <header class="header">
      <div class="brand"><span class="brand-mark"></span><span class="brand-name">corvane australia</span></div>
      <div class="quick" style="left:467px"><div class="icon icon-quote" role="img" aria-label="Quote form icon"></div>GET A QUOTE</div>
      <div class="quick" style="left:617px"><div class="icon icon-raters" role="img" aria-label="Energy raters icon"></div>ENERGY RATERS<small>ADD YOUR BUSINES</small></div>
      <div class="quick" style="left:783px"><div class="icon icon-board" role="img" aria-label="Job board checklist icon"></div>ACTIVE JOB BOARD</div>
    </header>
    <nav class="nav"><span>HOME</span><i>|</i><span>HOW IT WORKS?</span><i>|</i><span>ABOUT US</span><i>|</i><span>TESTIMONIALS</span><i>|</i><span>CONTACT US</span></nav>
    <div class="hero">
      <div class="step" style="left:18px"><span class="step-num">1</span><div class="step-text"><b>POST</b>A JOB</div></div>
      <div class="step" style="left:210px"><span class="step-num">2</span><div class="step-text"><b>GET</b>AS MANY<br>QUOTES AS YOU LIKE</div></div>
      <div class="step" style="left:405px"><span class="step-num">3</span><div class="step-text"><b>SELECT</b>ENERGY QUOTE<br>THAT SUITS</div></div>
      <div class="step" style="left:594px"><span class="step-num">4</span><div class="step-text"><b>APPROVE</b>PAYMENT</div></div>
      <div class="step" style="left:788px"><span class="step-num">5</span><div class="step-text"><b>RECEIVE</b>RATING</div></div>
    </div>
    <div class="hero-fade"></div>

    <h1 class="content-title" style="top:456px">Welcome To Our Site</h1>
    <div class="intro">
      <p>corvane australia is Australia's leading professional energy rating consultancy firm specializing in large scaled residential and commercial energy rating logistics.</p>
      <p>We have professional and accredited energy raters in all States and Territories ready and waiting to provide quotes for and perform your energy rating jobs!</p>
      <p>It's Free, Fast and Easy to use and you get the best price and turnaround time that suits you!!</p>
    </div>
    <div class="team-photo" role="img" aria-label="Photo of the business team seated at a meeting table"></div>
    <p class="wide" style="top:677px">Register with us, upload your job and specifications, and sit back and watch as energy raters provide quotes for your work!</p>
    <ul class="benefits">
      <li>Get the best priced quotes for your energy ratings</li>
      <li>Save time by listing a job to get many quotes</li>
      <li>Monitor your jobs and quotes on your own job board</li>
      <li>Be notified via email of all new quotes as they come in</li>
      <li>Be able to specify your desired turnaround times</li>
      <li>Accessible anytime and anywhere</li>
      <li>Choose a deadline for energy raters to supply quotes</li>
      <li>Have access to many qualified energy raters in your state all quoting for Work</li>
      <li>Be able to track your jobs and pay online</li>
      <li>Provide feedback on energy raters</li>
    </ul>
    <p class="wide" style="top:1005px">Its totally free to be registered with us and there is no obligations or hidden catches! So if you wish to utilise the amazing opportunity register now! This new website will be going live on the (insert date) so be ready to save some money!</p>

    <aside class="box" style="top:457px;height:208px">
      <h3>Member Area:</h3>
      <label>Login id</label><div class="field"></div>
      <label>Password</label><div class="field"></div>
      <p class="forgot">Forgot Pasword?</p>
      <span class="btn">Sign in</span>
    </aside>
    <aside class="box" style="top:701px;height:316px">
      <h3>Testimonials:</h3>
      <p class="testimonial">Lorem Ipsum is simply dummy text of the printing and typesetting industry. Lorem Ipsum has been the industry's standard dummy text ever since the 1500s.<cite>By: Reid Falcon</cite></p>
      <p class="testimonial">When an unknown printer took a galley of type and scrambled it to make a type specimen book. It has survived not only five centuries.<cite>By: Tomas Quill</cite></p>
    </aside>

    <footer class="footer" style="top:1119px"><span>Home</span>|<span>How it works?</span>|<span>About Us</span>|<span>Testimonials</span>|<span>Contact Us</span></footer>
  </div>
</section>

<div class="label-band" style="top:1283px;height:170px">INNER PAGE</div>

<section class="site" style="top:1453px;height:1319px">
  <div class="green-bar"></div>
  <div class="dark-band"></div>
  <div class="page" style="height:1299px">
    <header class="header">
      <div class="brand"><span class="brand-mark"></span><span class="brand-name">corvane australia</span></div>
      <div class="quick" style="left:467px"><div class="icon icon-quote" role="img" aria-label="Quote form icon"></div>GET A QUOTE</div>
      <div class="quick" style="left:617px"><div class="icon icon-raters" role="img" aria-label="Energy raters icon"></div>ENERGY RATERS<small>ADD YOUR BUSINES</small></div>
      <div class="quick" style="left:783px"><div class="icon icon-board" role="img" aria-label="Job board checklist icon"></div>ACTIVE JOB BOARD</div>
    </header>
    <nav class="nav"><span>HOME</span><i>|</i><span>HOW IT WORKS?</span><i>|</i><span>ABOUT US</span><i>|</i><span>TESTIMONIALS</span><i>|</i><span>CONTACT US</span></nav>
    <div class="hero">
      <div class="step" style="left:18px"><span class="step-num">1</span><div class="step-text"><b>POST</b>A JOB</div></div>
      <div class="step" style="left:210px"><span class="step-num">2</span><div class="step-text"><b>GET</b>AS MANY<br>QUOTES AS YOU LIKE</div></div>
      <div class="step" style="left:405px"><span class="step-num">3</span><div class="step-text"><b>SELECT</b>ENERGY QUOTE<br>THAT SUITS</div></div>
      <div class="step" style="left:594px"><span class="step-num">4</span><div class="step-text"><b>APPROVE</b>PAYMENT</div></div>
      <div class="step" style="left:788px"><span class="step-num">5</span><div class="step-text"><b>RECEIVE</b>RATING</div></div>
    </div>
    <div class="hero-fade"></div>

    <h1 class="content-title" style="top:455px;font-weight:700;font-size:28px">My Acount</h1>
    <div class="account">
      <div class="account-labels">Company Details:<br><span style="line-height:17px;display:block">Contact Person:<br>Email Address:</span>Street Address:<br><br>Suburb:<br>State:<br>Postcode:</div>
      <div class="account-values">Sam Varley<br><br>Level 1<br>218 Harlow Street<br>Ashmere<br>VIC<br>3004</div>
    </div>

    <div class="tabs">
      <div class="tab active">JOBS FOR QUOTING</div>
      <div class="tab">ACTIVE JOBS</div>
      <div class="tab">COMPLETED JOBS</div>
    </div>
    <div class="jobs-panel">
      <table class="jobs">
        <tr><th style="width:152px">Job</th><th style="width:134px">Quote Number</th><th style="width:97px">Price</th><th style="width:110px">Total Price</th><th style="width:134px">Turnaround<br>Time</th><th style="width:127px">Rework Price</th><th>Energy Raters<br>Accreditation</th></tr>
        <tr><td><div></div></td><td><div>111111</div></td><td><div>$155.00</div></td><td><div>$180.65</div></td><td><div>1-5 days</div></td><td><div>$120.00</div></td><td><div>VIC</div></td></tr>
        <tr><td><div></div></td><td><div>111156</div></td><td><div>$250.00</div></td><td><div>$265.00</div></td><td><div>5-10 days</div></td><td><div>$150.00</div></td><td><div>QLD</div></td></tr>
        <tr><td><div></div></td><td><div>111186</div></td><td><div>$125.00</div></td><td><div>$129.65</div></td><td><div>2 weeks</div></td><td><div>$100.00</div></td><td><div>SA</div></td></tr>
        <tr><td><div></div></td><td><div></div></td><td><div></div></td><td><div></div></td><td><div></div></td><td><div></div></td><td><div></div></td></tr>
        <tr><td><div></div></td><td><div></div></td><td><div></div></td><td><div></div></td><td><div></div></td><td><div></div></td><td><div></div></td></tr>
        <tr><td><div></div></td><td><div>111111</div></td><td><div>$155.00</div></td><td><div>$180.65</div></td><td><div>1-5 days</div></td><td><div>$120.00</div></td><td><div>VIC</div></td></tr>
        <tr><td><div></div></td><td><div>111156</div></td><td><div>$250.00</div></td><td><div>$265.00</div></td><td><div>5-10 days</div></td><td><div>$150.00</div></td><td><div>QLD</div></td></tr>
        <tr><td><div></div></td><td><div>111186</div></td><td><div>$125.00</div></td><td><div>$129.65</div></td><td><div>2 weeks</div></td><td><div>$100.00</div></td><td><div>SA</div></td></tr>
        <tr><td><div></div></td><td><div>111313</div></td><td><div>$350.00</div></td><td><div>$354.65</div></td><td><div>Aluminum</div></td><td><div>Doors</div></td><td><div>Standard</div></td></tr>
        <tr><td><div></div></td><td><div></div></td><td><div></div></td><td><div></div></td><td><div></div></td><td><div></div></td><td><div></div></td></tr>
        <tr><td><div></div></td><td><div></div></td><td><div></div></td><td><div></div></td><td><div></div></td><td><div></div></td><td><div></div></td></tr>
      </table>
    </div>

    <footer class="footer" style="top:1259px;height:40px"><span>Home</span>|<span>How it works?</span>|<span>About Us</span>|<span>Testimonials</span>|<span>Contact Us</span></footer>
  </div>
</section>

</body>
</html>
```